Venture 482 - Lumora Book Cover

I am looking for a Lumora book cover for my book about "Venture 482".
The Book is Titled:
Venture 482 Ascended
Shaping Outcomes: Paths To Unlocking Cosmic Truths
Author is Dorian Pell
Here is a book description that may help you understand more about it:
Inspired by the genius of Edwin Marlowe, this comprehensive guide delves into the ancient wisdom and cutting-edge science behind the 482 method, a powerful tool for manifesting your desires. Whether you're seeking personal growth, financial success, or spiritual enlightenment, this book provides advanced techniques and methods to transform your dreams into reality.
Any questions please ask.
Thanks
Owen

```html
<!DOCTYPE html>
<html lang="en">
<head>
<meta charset="utf-8">
<title>Venture 482 Ascended – Dorian Pell</title>
<link rel="stylesheet" href="https://fonts.googleapis.com/css2?family=Montserrat:wght@300;400&family=Poppins:wght@700;800&display=swap">
<style>
  :root {
    --page-bg: #ececec;
    --plum-deep: #3a1d38;
    --plum: #7a2f68;
    --mist-pink: #d8a6c6;
    --mist-blue: #a9c6d8;
    --magenta: #c2387c;
    --magenta-deep: #6e2560;
    --peach: #fde6d6;
    --ice: #e8f4fc;
    --indigo: #3b3f93;
    --white: #ffffff;
  }
  * { box-sizing: border-box; margin: 0; padding: 0; }
  html, body {
    width: 1200px;
    height: 1131px;
    overflow: hidden;
    background: var(--page-bg);
  }
  .book-cover {
    position: absolute;
    left: 243px;
    top: 30px;
    width: 714px;
    height: 1071px;
    overflow: hidden;
    border-radius: 6px;
  }
  .cover-art {
    position: absolute;
    inset: 0;
    background: linear-gradient(180deg,
      var(--plum-deep) 0%,
      var(--plum) 22%,
      var(--mist-pink) 50%,
      var(--mist-blue) 62%,
      var(--magenta) 78%,
      var(--magenta-deep) 100%);
  }
  .author {
    position: absolute;
    top: 70px;
    width: 100%;
    text-align: center;
    font-family: "Montserrat", sans-serif;
    font-weight: 300;
    font-size: 40px;
    letter-spacing: 0.32em;
    padding-left: 0.32em;
    color: var(--peach);
  }
  .title-block {
    position: absolute;
    top: 206px;
    width: 100%;
    text-align: center;
    font-family: "Poppins", sans-serif;
  }
  .title-word {
    display: block;
    font-weight: 800;
    font-size: 92px;
    line-height: 1;
    letter-spacing: -0.04em;
    color: var(--peach);
    text-shadow: 0 4px 10px rgba(60, 20, 50, 0.35);
  }
  .title-number {
    display: block;
    margin-top: -14px;
    font-weight: 700;
    font-size: 278px;
    line-height: 0.9;
    letter-spacing: -0.03em;
    color: var(--ice);
    text-shadow: 0 8px 18px rgba(60, 20, 50, 0.4);
  }
  .title-tag {
    display: block;
    margin-top: 16px;
    font-weight: 700;
    font-size: 50px;
    line-height: 1;
    letter-spacing: 0.42em;
    padding-left: 0.42em;
    color: var(--indigo);
  }
  .subtitle {
    position: absolute;
    top: 928px;
    width: 100%;
    text-align: center;
    font-family: "Montserrat", sans-serif;
    color: var(--white);
  }
  .subtitle-lead {
    display: block;
    font-weight: 400;
    font-size: 26px;
    line-height: 1.2;
  }
  .subtitle-line {
    display: block;
    font-weight: 400;
    font-size: 24px;
    line-height: 1.3;
  }
</style>
</head>
<body>
  <main class="book-cover">
    <div class="cover-art" role="img" aria-label="Dreamlike pink and violet city of tall towers above the clouds, a lone figure in a hoodie standing on a mirrored cloud floor"></div>
    <p class="author">DORIAN PELL</p>
    <h1 class="title-block">
      <span class="title-word">VENTURE</span>
      <span class="title-number">482</span>
      <span class="title-tag">ASCENDED</span>
    </h1>
    <p class="subtitle">
      <span class="subtitle-lead">SHAPING OUTCOMES:</span>
      <span class="subtitle-line">Paths to unlocking</span>
      <span class="subtitle-line">cosmic truths</span>
    </p>
  </main>
</body>
</html>
```